Cat-products company needs smart, yet endearing, business card

We need a business card design for a new, but up-and-running, business based in Honolulu, Hawaii. The business is Purrnest Nook Co. Our first product is the most environmentally-friendly cat grass kit ever seen on the planet. Future products, currently in the R&D phase, will include a variety of exciting cat scratchers. We also do consulting work to help apartment-dwellers make their home more cat-friendly and, in the future, plan on doing full, custom installs of structure to create high walkways for cats.

Target Market(s)

Middle-aged, apartment-dwelling, middle-class workers who own 1 or more cats and who dote on them.

Industry/Entity Type

Pet Care

Contact Information for Business Card

A striking, professional, yet warm and friendly design is what we're after.

Font styles to use
Serif
Sans Serif
Other font styles liked:
• Comfortaa

Colors

Designer to choose colors to be used in the design.

Requirements
Must have
• The company logo: (see attachment)
• The company name: Purrnest Nook Co
• The web address: www.purrnestnookco.com
• Email: support@purrnestnookco.com
• Phone: +1 (808) 571 6023
• Update (Fri Jun 30 3017 7:45pm Hawaii Time) I would like, is possible, uploaded picture of the cat grass kit on the back of the card with some text along the lines of: Purrnest Nook Co - Maker Of The Leafiest Feline Sprout Set Yet
Nice to have
• A cat picture, cartoon, real or silhouette that illustrates cats in action and/or relaxing; ie using the apartment space to live, play and relax in and being well-contented.
• Most of the website is done in the font: Comfortaa. It might be nice to continue using this for brand consistency.
Should not have
• Hard-to-read fonts.

```html
<!DOCTYPE html>
<html lang="en">
<head>
<meta charset="utf-8">
<title>Purrnest Nook Co — Business Card</title>
<link href="https://fonts.googleapis.com/css2?family=Open+Sans:wght@400;600;700&display=swap" rel="stylesheet">
<style>
  :root {
    --bg: #3b3330;
    --card: #141414;
    --card-edge: #1d1d1d;
    --amber: #f6a823;
    --cocoa: #6b4538;
    --ink: #f2f2f2;
    --muted: #8a8a8a;
    --emboss: #2a2a2a;
    --dot-a: #c0392b;
    --dot-b: #1f5f99;
    --dot-c: #2779b8;
    --dot-d: #1a6aa3;
  }
  * { margin: 0; padding: 0; box-sizing: border-box; }
  html, body { width: 1200px; height: 864px; overflow: hidden; }
  body {
    background: var(--bg);
    font-family: "Open Sans", Arial, sans-serif;
    position: relative;
  }
  .card {
    position: absolute;
    width: 540px;
    height: 309px;
    background: var(--card);
    border: 1px solid var(--card-edge);
    border-radius: 3px;
    box-shadow: 0 12px 30px rgba(0,0,0,.45);
  }
  /* back side */
  .card--back { left: 40px; top: 150px; }
  .back-mark {
    position: absolute;
    left: 90px; top: 110px;
    display: flex; align-items: center; gap: 12px;
    color: var(--emboss);
    font-weight: 700;
    font-size: 30px;
    letter-spacing: .5px;
  }
  .back-mark .square {
    width: 26px; height: 26px; background: var(--emboss);
  }
  .back-url {
    position: absolute;
    left: 90px; top: 200px;
    color: var(--muted);
    font-size: 14px;
    letter-spacing: 4px;
  }
  .social-dots {
    position: absolute;
    right: 28px; top: 24px;
    display: flex; gap: 3px;
  }
  .social-dots span {
    width: 14px; height: 14px; border-radius: 50%;
  }
  .social-dots span:nth-child(1) { background: var(--dot-a); }
  .social-dots span:nth-child(2) { background: var(--dot-b); }
  .social-dots span:nth-child(3) { background: var(--dot-c); }
  .social-dots span:nth-child(4) { background: var(--dot-d); }

  /* front side */
  .card--front { left: 620px; top: 405px; }
  .brand {
    position: absolute;
    left: 36px; top: 108px;
    width: 230px;
    display: flex; align-items: center; gap: 10px;
  }
  .brand .square {
    flex: none; width: 22px; height: 22px; background: var(--cocoa);
  }
  .brand-name {
    color: var(--amber);
    font-weight: 700;
    font-size: 26px;
    line-height: 1.1;
  }
  .divider {
    position: absolute;
    left: 280px; top: 40px;
    width: 1px; height: 230px;
    background: linear-gradient(to bottom, transparent, #d8d8d8 30%, #d8d8d8 70%, transparent);
  }
  .details {
    position: absolute;
    left: 300px; top: 62px;
    color: var(--ink);
    font-size: 14px;
    line-height: 1.35;
  }
  .person-name {
    color: var(--cocoa);
    font-weight: 600;
    font-size: 13px;
    text-transform: uppercase;
  }
  .person-role {
    color: var(--amber);
    font-weight: 600;
    font-size: 14px;
    margin-bottom: 10px;
  }
  .contact-line { display: flex; align-items: center; gap: 6px; }
  .contact-line svg { width: 11px; height: 11px; flex: none; }
  .contact-line .spacer { width: 11px; flex: none; }
</style>
</head>
<body>
  <section class="card card--back" aria-label="Card back">
    <div class="social-dots"><span></span><span></span><span></span><span></span></div>
    <div class="back-mark"><span class="square"></span>Purrnest Nook Co</div>
    <p class="back-url">www.purrnestnookco.com</p>
  </section>

  <section class="card card--front" aria-label="Card front">
    <div class="brand">
      <span class="square"></span>
      <span class="brand-name">Purrnest Nook Co</span>
    </div>
    <div class="divider"></div>
    <div class="details">
      <p class="person-name">Maya Kealoha</p>
      <p class="person-role">CEO/FOUNDER</p>
      <p class="contact-line">
        <svg viewBox="0 0 12 12" fill="#8a8a8a"><path d="M6 1 1 5.5h1.5V11h7V5.5H11z"/></svg>
        2418 Lanai Breeze Way
      </p>
      <p class="contact-line"><span class="spacer"></span>Kailua, Hawaii 96734</p>
      <p class="contact-line">
        <svg viewBox="0 0 12 12" fill="#8a8a8a"><path d="M3 1h2l1 3-1.5 1a6 6 0 0 0 2.5 2.5L8 6l3 1v2a2 2 0 0 1-2 2A8 8 0 0 1 1 3a2 2 0 0 1 2-2z"/></svg>
        +1 (808) 571 6023
      </p>
      <p class="contact-line">
        <svg viewBox="0 0 12 12" fill="#8a8a8a"><rect x="1" y="2.5" width="10" height="7" rx="1"/><path d="M1 3l5 3.5L11 3" stroke="#141414" fill="none"/></svg>
        support@purrnestnookco.com
      </p>
      <p class="contact-line">
        <svg viewBox="0 0 12 12" fill="none" stroke="#8a8a8a"><circle cx="6" cy="6" r="4.5"/><path d="M1.5 6h9M6 1.5c-2 2.5-2 6.5 0 9M6 1.5c2 2.5 2 6.5 0 9"/></svg>
        www.purrnestnookco.com
      </p>
    </div>
  </section>
</body>
</html>
```